Business Card for Meadow Ranger-Eco Friendly Organic Clothing Brand

We are looking for an amazing business card for our eco friendly, organic clothing brand. We are thinking maybe a business card with a peel off sticker on the back, since our hanging clothing tag is a peel off sticker on the back. I will attach our hang tag so we can make sure we stay in line with our design. I've also attached a bag we are doing because I do like the scattered emblem look as well.

```html
<!DOCTYPE html>
<html lang="en">
<head>
<meta charset="utf-8">
<title>Meadow Ranger – Business Card</title>
<link rel="stylesheet" href="https://fonts.googleapis.com/css2?family=Open+Sans:wght@400;600;700&display=swap">
<style>
  :root {
    --page-bg: #ecebe8;
    --card-dark: #272a22;
    --card-gold: #b8913f;
    --gold-light: #d9b45c;
    --swoosh-white: #f2f2f0;
    --text-white: #ffffff;
    --tag-grey: #e6e6e4;
    --pattern-dark: #3a3c37;
  }
  html, body {
    margin: 0;
    padding: 0;
    width: 1200px;
    height: 782px;
    overflow: hidden;
    background: var(--page-bg);
    font-family: "Open Sans", Arial, sans-serif;
  }
  .stage {
    position: relative;
    width: 1200px;
    height: 782px;
  }
  .card-front {
    position: absolute;
    left: 135px;
    top: 340px;
    width: 553px;
    height: 310px;
    border-radius: 10px;
    overflow: hidden;
    background: var(--card-dark);
  }
  .card-front .swoosh {
    position: absolute;
    inset: 0;
  }
  .brand-name {
    position: absolute;
    left: 24px;
    top: 24px;
    display: flex;
    align-items: center;
    gap: 10px;
    font-size: 30px;
    font-weight: 700;
    color: var(--gold-light);
    letter-spacing: 0.5px;
  }
  .brand-dot {
    width: 34px;
    height: 34px;
    border-radius: 50%;
    background: var(--gold-light);
  }
  .person {
    position: absolute;
    right: 64px;
    top: 18px;
    text-align: right;
  }
  .person-name {
    margin: 0;
    font-size: 18px;
    font-weight: 700;
    color: var(--text-white);
    letter-spacing: 0.3px;
  }
  .person-title {
    margin: 1px 0 0;
    font-size: 13px;
    color: var(--card-gold);
  }
  .person-address {
    margin: 12px 0 0;
    font-size: 13px;
    color: var(--text-white);
  }
  .tag-emblem {
    position: absolute;
    left: 20px;
    top: 138px;
    width: 153px;
    height: 70px;
    background: var(--tag-grey);
  }
  .tag-emblem .tag-inner {
    position: absolute;
    left: 18px;
    top: 9px;
    width: 115px;
    height: 52px;
    border-radius: 6px;
    background: linear-gradient(90deg, #2e2f28, #4a4330);
    border: 2px solid var(--gold-light);
    box-sizing: border-box;
  }
  .divider {
    position: absolute;
    left: 20px;
    top: 208px;
    width: 478px;
    height: 2px;
    background: var(--swoosh-white);
  }
  .contacts {
    position: absolute;
    left: 20px;
    top: 242px;
    margin: 0;
    padding: 0;
    list-style: none;
    font-size: 13px;
    line-height: 17px;
    color: var(--text-white);
  }
  .contacts li {
    display: flex;
    align-items: center;
    gap: 8px;
  }
  .contacts svg {
    width: 11px;
    height: 11px;
    fill: none;
    stroke: var(--card-gold);
    stroke-width: 1.6;
  }
  .card-back {
    position: absolute;
    left: 710px;
    top: 84px;
    width: 327px;
    height: 566px;
    border-radius: 12px;
    overflow: hidden;
    background: var(--pattern-dark);
  }
  .back-pattern {
    position: absolute;
    inset: 0;
    background: linear-gradient(160deg, #40423c 0%, #353731 55%, #3d3f39 100%);
  }
  .back-band {
    position: absolute;
    left: 0;
    right: 0;
    top: 413px;
    height: 62px;
    border-top: 3px solid var(--gold-light);
    border-bottom: 3px solid var(--gold-light);
    box-sizing: border-box;
    background: var(--pattern-dark);
    display: flex;
    align-items: center;
    justify-content: center;
  }
  .back-band-name {
    font-size: 36px;
    font-weight: 600;
    color: var(--gold-light);
    white-space: nowrap;
  }
</style>
</head>
<body>
<main class="stage">

  <section class="card-front">
    <svg class="swoosh" width="553" height="310" viewBox="0 0 553 310" aria-hidden="true">
      <path d="M505 0 Q565 160 370 310 L553 310 L553 0 Z" fill="var(--swoosh-white)"/>
      <path d="M532 0 Q580 180 388 310 L553 310 L553 0 Z" fill="var(--card-gold)"/>
    </svg>

    <div class="brand-name"><span class="brand-dot"></span>Meadow Ranger</div>

    <div class="person">
      <p class="person-name">Daniel Reyes</p>
      <p class="person-title">Director</p>
      <p class="person-address">Coral Bay, FL&nbsp; 33401</p>
    </div>

    <div class="tag-emblem" role="img" aria-label="Hang tag emblem with meditating figure, heart, peace sign and peace hand icons">
      <div class="tag-inner"></div>
    </div>

    <div class="divider"></div>

    <ul class="contacts">
      <li>
        <svg viewBox="0 0 12 12"><path d="M2 1 L4.5 1 L5.5 3.5 L4 4.8 Q5 7 7.2 8 L8.5 6.5 L11 7.5 L11 10 Q6 11 3 8 Q1 5 2 1 Z"/></svg>
        (877) 555-0142
      </li>
      <li>
        <svg viewBox="0 0 12 12"><circle cx="6" cy="6" r="5"/><path d="M1 6 H11 M6 1 Q3 6 6 11 M6 1 Q9 6 6 11"/></svg>
        www.meadowranger.com
      </li>
      <li>
        <svg viewBox="0 0 12 12"><rect x="1" y="2.5" width="10" height="7"/><path d="M1 2.5 L6 6.5 L11 2.5"/></svg>
        customerlove@meadowranger.com
      </li>
    </ul>
  </section>

  <section class="card-back">
    <div class="back-pattern" role="img" aria-label="Scattered gold word pattern: love, peace, inspire, live, om, namaste, hearts and peace signs on dark satin"></div>
    <div class="back-band">
      <span class="back-band-name">Meadow Ranger</span>
    </div>
  </section>

</main>
</body>
</html>
```